Business Card for premium dental clinic

We are a premium dental clinic based in Brasov, Romania with more than 15 year on the market, providing quality dental treatment made by a team of more specialized dentists, working with modern equipment as a solution to beautiful and healthy teeth.

Our current logo for the clinic use 2 square with colors black and gold - dr Ternisu - studio, using family fonts Bodoni, Myriad Pro and Segoe Print.
Depending on the printing we used some gold CMYK background or gold foil picture background or a gold gradient.
We want a business card:
- eye catching business card
- distinguished business card
- premium design
- to keep the color scheme of black and gold
- to attract the customers to spent time reading the information
- modern concept

```html
<!DOCTYPE html>
<html lang="en">
<head>
<meta charset="utf-8">
<title>Calden Dental Clinic – Business Card</title>
<link rel="stylesheet" href="https://fonts.googleapis.com/css2?family=Montserrat:wght@400;600;700&display=swap">
<style>
  :root {
    --page-bg: #3a2c25;
    --card-bg: #303032;
    --gold: #d9a832;
    --gold-light: #f0cf6a;
    --white: #ffffff;
    --muted-gold: #c9982c;
  }
  * { margin: 0; padding: 0; box-sizing: border-box; }
  html, body {
    width: 1200px; height: 800px; overflow: hidden;
    background: var(--page-bg);
    font-family: "Montserrat", sans-serif;
  }
  .sheet {
    width: 1200px; height: 800px;
    display: flex; align-items: center; justify-content: center; gap: 60px;
  }
  .card {
    position: relative;
    width: 525px; height: 300px;
    background: var(--card-bg);
    border: 2px solid var(--gold);
    border-radius: 3px;
    box-shadow: 0 14px 30px rgba(0,0,0,0.35);
    overflow: hidden;
  }

  /* brand lockup */
  .brand { display: flex; align-items: center; gap: 12px; color: var(--gold); font-weight: 600; }
  .brand-mark { width: 14px; height: 14px; border-radius: 50%; background: var(--gold); flex: none; }
  .brand-name { line-height: 1.1; }
  .brand-name small { display: block; font-size: 0.42em; letter-spacing: 0.18em; text-transform: uppercase; margin-top: 4px; }

  .card-front .brand {
    position: absolute; left: 50%; top: 50%; transform: translate(-50%, -50%);
    font-size: 46px;
  }
  .card-front .brand-mark { width: 18px; height: 18px; }

  /* back */
  .holder { position: absolute; left: 34px; top: 96px; }
  .holder-name { color: var(--white); font-weight: 700; font-size: 19px; letter-spacing: 0.01em; }
  .holder-role { color: var(--muted-gold); font-size: 10px; margin-top: 2px; }

  .divider {
    position: absolute; left: 34px; right: 34px; top: 152px;
    height: 1.5px; background: var(--gold);
  }

  .contacts { position: absolute; left: 34px; top: 170px; list-style: none; }
  .contacts li {
    display: flex; align-items: center; gap: 10px;
    color: var(--gold); font-size: 12px; margin-bottom: 9px;
  }
  .contacts svg { width: 12px; height: 12px; fill: var(--white); flex: none; }

  .card-back .brand { position: absolute; right: 36px; top: 92px; font-size: 28px; }

  .address {
    position: absolute; right: 36px; bottom: 26px;
    text-align: right; color: var(--gold); font-size: 12px; line-height: 1.4;
  }
</style>
</head>
<body>
<main class="sheet">

  <section class="card card-front" aria-label="Card front">
    <div class="brand">
      <span class="brand-mark"></span>
      <span class="brand-name">Calden<small>Dental Clinic</small></span>
    </div>
  </section>

  <section class="card card-back" aria-label="Card back">
    <div class="holder">
      <p class="holder-name">dr Ternisu</p>
      <p class="holder-role">Manager</p>
    </div>

    <div class="brand">
      <span class="brand-mark"></span>
      <span class="brand-name">Calden<small>Dental Clinic</small></span>
    </div>

    <div class="divider"></div>

    <ul class="contacts">
      <li>
        <svg viewBox="0 0 24 24" aria-hidden="true"><path d="M6.6 10.8c1.4 2.8 3.8 5.1 6.6 6.6l2.2-2.2c.3-.3.7-.4 1-.2 1.1.4 2.3.6 3.6.6.6 0 1 .4 1 1V20c0 .6-.4 1-1 1C10.6 21 3 13.4 3 4c0-.6.4-1 1-1h3.5c.6 0 1 .4 1 1 0 1.3.2 2.5.6 3.6.1.3 0 .7-.2 1z"/></svg>
        555-014-2100
      </li>
      <li>
        <svg viewBox="0 0 24 24" aria-hidden="true"><path d="M2 5h20v14H2z M4 7v.5l8 5 8-5V7z" fill-rule="evenodd"/></svg>
        hello@caldendental.com
      </li>
      <li>
        <svg viewBox="0 0 24 24" aria-hidden="true"><path d="M12 2a10 10 0 1 0 0 20 10 10 0 0 0 0-20zm0 2a8 8 0 0 1 7.7 6H4.3A8 8 0 0 1 12 4zm0 16a8 8 0 0 1-7.7-6h15.4A8 8 0 0 1 12 20z"/></svg>
        www.caldendental.com
      </li>
    </ul>

    <p class="address">Your address, city<br>state, ZIP 0000</p>
  </section>

</main>
</body>
</html>
```